Business card design needed

I would like a one sided black business card with the information provided above. Refer to my website www.brightvolleyracquets.com.au for an example of colors I have used for my site, would like to keep this consistent for my business cards also, I will upload my logo below.

I am a new small business that provides tennis customers with racquet re stringing, tennis strings and accessories.

Industry/Entity Type

Small Business

Contact Information for Business Card

Bright Volley Tennis

Owen Whitby
Managing Director

brightvolleyracquets@mailbox.example
www.brightvolleyracquets.com.au
0491 726 305

Racquet Restringing/Tennis Strings/Accessories

Requirements
Must have
• Must have my logo and card must be black

```html
<!DOCTYPE html>
<html lang="en">
<head>
<meta charset="utf-8">
<title>Bright Volley Tennis – Business Card</title>
<link href="https://fonts.googleapis.com/css2?family=Source+Sans+3:wght@400;600;700&display=swap" rel="stylesheet">
<style>
  :root {
    --backdrop: #e8e5e0;
    --card-black: #000000;
    --lime: #b9d82c;
    --divider: #2f4a50;
    --ink: #111111;
    --icon: #333333;
    --white: #ffffff;
  }
  * { box-sizing: border-box; margin: 0; padding: 0; }
  html, body {
    width: 1200px;
    height: 475px;
    overflow: hidden;
    background: var(--backdrop);
    font-family: "Source Sans 3", "Myriad Pro", Arial, sans-serif;
  }
  .canvas {
    position: relative;
    width: 1200px;
    height: 475px;
  }
  .card {
    position: absolute;
    width: 547px;
    height: 312px;
    border-radius: 14px;
    overflow: hidden;
    background: var(--card-black);
  }
  .card--front { left: 26px; top: 81px; }
  .card--back  { left: 607px; top: 85px; }

  /* brand mark: name with one plain circle */
  .brand {
    position: absolute;
    display: flex;
    align-items: center;
    gap: 9px;
    color: var(--lime);
    font-weight: 700;
    white-space: nowrap;
  }
  .brand__dot {
    flex: none;
    border-radius: 50%;
    background: var(--lime);
  }
  .card--front .brand {
    left: 0;
    width: 288px;
    top: 136px;
    justify-content: center;
    font-size: 22px;
  }
  .card--front .brand__dot { width: 20px; height: 20px; }
  .card--back .brand {
    left: 0;
    width: 100%;
    top: 118px;
    justify-content: center;
    font-size: 34px;
  }
  .card--back .brand__dot { width: 30px; height: 30px; }

  /* front: split layout */
  .card__divider {
    position: absolute;
    left: 288px;
    top: 0;
    width: 5px;
    height: 100%;
    background: var(--divider);
  }
  .card__info {
    position: absolute;
    left: 293px;
    top: 0;
    right: 0;
    bottom: 0;
    background: var(--lime);
    color: var(--ink);
    padding: 84px 0 0 14px;
  }
  .person__name {
    font-size: 20px;
    font-weight: 400;
    text-transform: uppercase;
    letter-spacing: 0.2px;
    line-height: 1.1;
  }
  .person__title {
    font-size: 14px;
    margin-top: 3px;
  }
  .contact {
    list-style: none;
    margin-top: 58px;
  }
  .contact__item {
    display: flex;
    align-items: center;
    gap: 8px;
    font-size: 12.5px;
    letter-spacing: -0.1px;
    line-height: 20px;
    white-space: nowrap;
  }
  .contact__icon {
    width: 11px;
    height: 11px;
    flex: none;
  }

  /* back: website */
  .card__web {
    position: absolute;
    left: 0;
    width: 100%;
    top: 238px;
    text-align: center;
    color: var(--white);
    font-size: 14px;
    letter-spacing: 2px;
  }
</style>
</head>
<body>
<main class="canvas">

  <section class="card card--front" aria-label="Business card front">
    <div class="brand">
      <span class="brand__dot"></span>
      <span class="brand__name">Bright Volley Tennis</span>
    </div>
    <div class="card__divider"></div>
    <div class="card__info">
      <h1 class="person__name">Owen Whitby</h1>
      <p class="person__title">Managing Director</p>
      <ul class="contact">
        <li class="contact__item">
          <svg class="contact__icon" viewBox="0 0 12 12" aria-hidden="true">
            <path d="M2.5 0.8 L4.4 0.8 L5 3.4 L3.8 4.4 Q5 7 7.6 8.2 L8.6 7 L11.2 7.6 L11.2 9.5 Q11.2 11.2 9.5 11.2 Q0.8 10.6 0.8 2.5 Q0.8 0.8 2.5 0.8 Z" fill="var(--icon)"/>
          </svg>
          <span>0491 726 305</span>
        </li>
        <li class="contact__item">
          <svg class="contact__icon" viewBox="0 0 12 12" aria-hidden="true">
            <rect x="0.5" y="2" width="11" height="8" fill="var(--icon)"/>
            <path d="M0.5 2 L6 6.5 L11.5 2" fill="none" stroke="var(--lime)" stroke-width="1"/>
          </svg>
          <span>brightvolleyracquets@mailbox.example</span>
        </li>
        <li class="contact__item">
          <svg class="contact__icon" viewBox="0 0 12 12" aria-hidden="true">
            <circle cx="6" cy="6" r="5.2" fill="none" stroke="var(--icon)" stroke-width="1.2"/>
            <ellipse cx="6" cy="6" rx="2.3" ry="5.2" fill="none" stroke="var(--icon)" stroke-width="1"/>
            <path d="M0.8 6 H11.2" stroke="var(--icon)" stroke-width="1"/>
          </svg>
          <span>www.brightvolleyracquets.com.au</span>
        </li>
      </ul>
    </div>
  </section>

  <section class="card card--back" aria-label="Business card back">
    <div class="brand">
      <span class="brand__dot"></span>
      <span class="brand__name">Bright Volley Tennis</span>
    </div>
    <p class="card__web">www.brightvolleyracquets.com.au</p>
  </section>

</main>
</body>
</html>
```